Communication and Marketing agency needs a new presentation card

We are a group of communication and marketing agencies specialized in companies that are in the logistics and industrial sector. The head agency is TELVANO Grupo and the group consists of 4 agencies: TELVANO Media, TELVANO Digital, TELVANO Research and DifundeEnPantalla. We hace 4 offices in Spain (Madrid, Barcelona, Valencia and Murcia). We are looking for a clean and attractive design that transmits our experience, brand presence in the market and knowledge to those who receive the card.It has to maintain the colors of the logo that is attached.
Target Market(s)
logistics and industrial sector
Marketing department
Contact Information for Business Card
Clean and attractive design

```html
<!DOCTYPE html>
<html lang="en">
<head>
<meta charset="utf-8">
<title>TELVANO Grupo – Business Card</title>
<link rel="stylesheet" href="https://fonts.googleapis.com/css2?family=Oswald:wght@500&family=Fira+Sans:wght@400&display=swap">
<style>
  :root {
    --brand-red: #ad1e28;
    --ink: #2b2b2b;
    --paper: #ffffff;
    --backdrop: #a3a2a0;
  }
  * { margin: 0; padding: 0; box-sizing: border-box; }
  html, body { width: 1200px; height: 1200px; overflow: hidden; background: var(--backdrop); }
  .canvas { position: relative; width: 1200px; height: 1200px; }

  .card {
    position: absolute;
    left: 224px;
    width: 814px;
    height: 465px;
    border-radius: 30px;
  }
  .card--front { top: 76px; background: var(--paper); }
  .card--back { top: 658px; background: var(--brand-red); }

  .brand-name {
    position: absolute;
    font-family: "Oswald", sans-serif;
    font-weight: 500;
    font-size: 62px;
    line-height: 68px;
    text-align: right;
    letter-spacing: 1px;
  }
  .card--front .brand-name { right: 64px; top: 90px; color: var(--brand-red); }
  .card--back .brand-name { right: 202px; top: 166px; color: var(--paper); }

  .person {
    position: absolute;
    left: 66px;
    top: 260px;
  }
  .person__name {
    font-family: "Oswald", sans-serif;
    font-weight: 500;
    font-size: 36px;
    line-height: 40px;
    color: var(--ink);
    letter-spacing: 0.2px;
  }
  .person__name .first { color: var(--brand-red); }
  .person__role {
    font-family: "Fira Sans", sans-serif;
    font-size: 17px;
    color: var(--ink);
    margin-top: 2px;
  }

  .rule {
    position: absolute;
    width: 52px;
    height: 3px;
    background: var(--brand-red);
  }
  .rule--contact { left: 66px; top: 336px; }
  .rule--address { left: 553px; top: 336px; }

  .details {
    position: absolute;
    font-family: "Fira Sans", sans-serif;
    font-size: 17px;
    line-height: 23.5px;
    color: var(--ink);
    list-style: none;
  }
  .details--contact { left: 66px; top: 352px; }
  .details--address { left: 553px; top: 348px; }
  .details .label { color: var(--brand-red); }
  .details .accent { color: var(--brand-red); }
</style>
</head>
<body>
<main class="canvas">
  <section class="card card--front" aria-label="Business card front">
    <div class="brand-name">TELVANO<br>Grupo</div>

    <div class="person">
      <h1 class="person__name"><span class="first">LUCAS</span> MORENTE</h1>
      <p class="person__role">MANAGER</p>
    </div>

    <div class="rule rule--contact"></div>
    <ul class="details details--contact">
      <li><span class="label">P.</span> +(34) -915- 4402</li>
      <li><span class="label">F.</span> +(34) -915- 4402</li>
      <li>hola@telvanogrupo.es</li>
    </ul>

    <div class="rule rule--address"></div>
    <ul class="details details--address">
      <li>Calle Alcalá 214,</li>
      <li>28028 Madrid</li>
      <li>www.<span class="accent">telvanogrupo</span>.es</li>
    </ul>
  </section>

  <section class="card card--back" aria-label="Business card back">
    <div class="brand-name">TELVANO<br>Grupo</div>
  </section>
</main>
</body>
</html>
```